Modern Business Card

Modern professional business card with more than just logo and demographic info. Something memorable.

We are a trendy/modern chiropractic group with an emphasis on neurology, hence the minimalist-type brain logo. We want to convey that modern and technical aspect with professionalism and the elite nature of our practice environment.

```html
<!DOCTYPE html>
<html lang="en">
<head>
<meta charset="utf-8">
<title>Cadence Chiropractic – Business Card</title>
<link href="https://fonts.googleapis.com/css2?family=Cinzel:wght@400&family=Montserrat:wght@400;500&display=swap" rel="stylesheet">
<style>
  :root {
    --backdrop: #dcdcdc;
    --card: #ffffff;
    --brand-blue: #4a7fc4;
    --ink: #3a3a3a;
    --ink-dark: #1c1c1c;
    --rule: #555555;
  }
  * { box-sizing: border-box; margin: 0; padding: 0; }
  html, body {
    width: 1200px; height: 930px; overflow: hidden;
    background: var(--backdrop);
  }
  .canvas {
    position: relative; width: 1200px; height: 930px;
  }
  .card {
    position: absolute; top: 313px;
    width: 530px; height: 303px;
    background: var(--card);
    border-radius: 18px;
    overflow: hidden;
    box-shadow: 0 6px 18px rgba(0,0,0,0.12);
  }
  .card--front { left: 50px; }
  .card--back { left: 620px; }

  /* Front */
  .front-brand {
    position: absolute; left: 0; right: 0; top: 78px;
    display: flex; align-items: center; justify-content: center; gap: 18px;
  }
  .brand-dot {
    width: 62px; height: 62px; border-radius: 50%;
    background: var(--brand-blue);
  }
  .wordmark {
    font-family: "Cinzel", serif; font-weight: 400;
    line-height: 1;
  }
  .wordmark__top { display: block; font-size: 44px; letter-spacing: 1px; }
  .wordmark__bottom { display: block; font-size: 23px; letter-spacing: 1px; margin-top: 2px; }
  .wordmark--dark { color: var(--ink-dark); }
  .wordmark--blue { color: var(--brand-blue); }

  .front-band {
    position: absolute; left: 0; right: 0; top: 222px; height: 30px;
    background: var(--brand-blue);
    display: flex; align-items: center; justify-content: center;
    font-family: "Montserrat", sans-serif; font-size: 13px;
    letter-spacing: 1.5px; color: #fff;
  }
  .front-stripe {
    position: absolute; left: 0; right: 0; bottom: 0; height: 12px;
    background: var(--brand-blue);
  }

  /* Back */
  .back-mark {
    position: absolute; right: 52px; top: 24px;
    width: 120px; height: 120px; border-radius: 50%;
    background: var(--brand-blue);
  }
  .back-wordmark { position: absolute; left: 38px; top: 78px; }
  .back-wordmark .wordmark__top { font-size: 38px; }
  .back-wordmark .wordmark__bottom { font-size: 20px; }

  .person { position: absolute; left: 40px; top: 160px; }
  .person__name {
    font-family: "Cinzel", serif; font-size: 17px; color: var(--brand-blue);
    letter-spacing: 0.5px;
  }
  .person__role {
    font-family: "Montserrat", sans-serif; font-size: 12px; color: var(--ink);
    margin-top: 2px;
  }
  .divider {
    position: absolute; left: 40px; right: 40px; top: 200px;
    height: 1px; background: var(--rule);
  }
  .contacts {
    position: absolute; left: 40px; top: 212px; list-style: none;
    font-family: "Montserrat", sans-serif; font-size: 12.5px; color: var(--ink);
  }
  .contacts li { display: flex; align-items: center; gap: 10px; height: 20px; }
  .contacts svg { width: 12px; height: 12px; fill: none; stroke: var(--brand-blue); stroke-width: 1.6; }
  .accent { color: var(--brand-blue); }
  .address {
    position: absolute; right: 40px; top: 214px; text-align: right;
    font-family: "Montserrat", sans-serif; font-size: 12.5px; color: var(--ink);
    line-height: 19px;
  }
  .back-stripe {
    position: absolute; left: 0; right: 0; bottom: 0; height: 10px;
    background: var(--brand-blue);
  }
</style>
</head>
<body>
<main class="canvas">

  <section class="card card--front" aria-label="Card front">
    <div class="front-brand">
      <span class="brand-dot"></span>
      <div class="wordmark wordmark--dark">
        <span class="wordmark__top">CADENCE</span>
        <span class="wordmark__bottom">CHIROPRACTIC</span>
      </div>
    </div>
    <div class="front-band">www.cadencechiro.com</div>
    <div class="front-stripe"></div>
  </section>

  <section class="card card--back" aria-label="Card back">
    <span class="back-mark"></span>
    <div class="back-wordmark wordmark wordmark--blue">
      <span class="wordmark__top">CADENCE</span>
      <span class="wordmark__bottom">CHIROPRACTIC</span>
    </div>

    <div class="person">
      <div class="person__name">MARK ELLISON</div>
      <div class="person__role">Director</div>
    </div>
    <div class="divider"></div>

    <ul class="contacts">
      <li>
        <svg viewBox="0 0 12 12"><path d="M3 1.5 L4.5 4 L3.5 5 Q4.5 7.5 7 8.5 L8 7.5 L10.5 9 L9.5 10.5 Q4 10 1.5 3 Z"/></svg>
        (555) 214-3380
      </li>
      <li>
        <svg viewBox="0 0 12 12"><rect x="1.5" y="2.5" width="9" height="7"/><path d="M1.5 2.5 L6 6.5 L10.5 2.5"/></svg>
        hello@cadencechiro.com
      </li>
      <li>
        <svg viewBox="0 0 12 12"><circle cx="6" cy="6" r="4.5"/><path d="M1.5 6 H10.5 M6 1.5 Q3.5 6 6 10.5 M6 1.5 Q8.5 6 6 10.5"/></svg>
        <span>www.<span class="accent">cadencechiro</span>.com</span>
      </li>
    </ul>

    <address class="address" style="font-style: normal;">
      1187 Larkmoor Lane<br>
      Salem, OR 97302
    </address>

    <div class="back-stripe"></div>
  </section>

</main>
</body>
</html>
```